Need App for Impact Related Events

My app is to help with internal events. When you enter the prompted event code the next screen shows you everyone currently at the event. It will give you the ability to Start a conversation with someone you met at that event, or signal it is your turn to send a message. The next screen is a message thread with that person. I am looking for a design that incorporates the colors and ‘feel good’ emotion of our logo. I have pieced together a pretty good interpretation of what I’m looking for in the attached mockup by slicing and dicing designs. I also attached our logo mascot.Screens (see attached mockups)

Note 1: I do not like the picture on the screen used in screen one because it makes it seem like a dating app. I attached an alternative photo that can be used or present different ideas.

Note 2: On the login/signup screen (screen 2) I need an additional first and last name for login, you can try to fit this on one login screen or present a two step signup screen where that is presented in the second screen.

READ MOCKUP GUIDELINES UNDER Must Haves

Target Market(s)

People attending internal social impact events

Industry/Entity Type

Charity

Font styles to use
Sans Serif

Colors
86cfc6

Requirements
Must have
• Follow the screen mockups attached to project
• PLEASE READ
• I have provided a relatively close design of what I’m looking for in the mockups. Some screens need to be followed more closely to my design mockup than other. I have listed a guide below how how closely you should follow my mockup design exactly. Overall I would like to see some ideas of incorporating a few accent colors so it doesn’t appear SO Blue. I also attached some app inspiration designs I found from around the web
• Screen Mockup Guideline Follow %
• Screen 1: 65% - mostly on target, would like to see ways to make it not SO Blue and possibly creative places to add some explainer text describing the app
• Screen 2: 50% - general design idea is here, but more open
• Screen 3: 35% - a lot more room for design influence
• Screen 4: 70% - mostly on target, a little room for design influence/color scheme ideas
• Screen 5-6: 25% - a lot of room for design change/ideas/influence
• Screen 7-8: 80% - already very close to what I need, maybe open to slight sizing and color scheme ideas
• Screen 9: 15% - the most open for influence, only the general functionality of the screen is communicated here
Nice to have
• Please Read Mockup Guideline above. In large part I am looking for something to use some nice accent colors so it is not overwhelmingly blue and bring the whole design into a seamless style.
Should not have

```html
<!DOCTYPE html>
<html lang="en">
<head>
<meta charset="utf-8">
<title>Who you've met – event chat screens</title>
<link href="https://fonts.googleapis.com/css2?family=Inter:wght@300;400;500&display=swap" rel="stylesheet">
<style>
  :root{
    --stage:#45b9fb;
    --white:#ffffff;
    --ink:#2d3440;
    --ink-soft:#3f4652;
    --muted:#8a9099;
    --line:#e3e5e8;
    --list-bg:#f7f8f9;
    --chat-bg:#f5f5f6;
    --blue:#3ab6f8;
    --blue-2:#2fd0fb;
    --orange:#fb9a33;
    --purple:#c97af8;
    --teal:#2ee0d0;
    --teal-2:#19d2c2;
    --red:#fb6460;
    --yellow:#fdd444;
  }
  *{box-sizing:border-box;margin:0;padding:0}
  html,body{width:1200px;height:1200px;overflow:hidden}
  body{background:var(--stage);font-family:"Inter",sans-serif;color:var(--ink);position:relative}
  .screen{position:absolute;top:76px;width:484px;height:1048px;background:var(--white);overflow:hidden;box-shadow:0 6px 18px rgba(0,60,120,.12)}
  .screen--contacts{left:82px}
  .screen--chat{left:634px}
  .status-bar{position:absolute;left:0;top:0;width:100%;height:50px}
  .status-bar__time{position:absolute;left:45px;top:20px;font-size:17px;font-weight:500;letter-spacing:-.2px}
  .status-bar__icons{position:absolute;right:28px;top:20px;display:flex;gap:6px;align-items:center}
  .nav-bar{position:absolute;left:0;top:50px;width:100%;height:63px;border-bottom:1px solid var(--line);background:var(--white)}
  .nav-bar__back{position:absolute;left:20px;top:22px}
  .nav-bar__title{position:absolute;left:148px;top:22px;display:flex;align-items:center;gap:10px;font-size:21px;font-weight:400;letter-spacing:-.3px}
  .brand-dot{width:26px;height:26px;border-radius:50%;background:var(--teal)}
  .nav-bar__actions{position:absolute;right:20px;top:18px;display:flex;gap:14px}
  .contact-list{position:absolute;left:0;top:113px;width:100%;height:803px;background:var(--list-bg)}
  .contact-card{position:absolute;left:21px;width:442px;height:114px;background:var(--white);border-radius:8px;box-shadow:0 2px 8px rgba(0,0,0,.04)}
  .contact-card__blob{position:absolute;left:0;top:0}
  .avatar{position:absolute;border-radius:50%;background:linear-gradient(145deg,#b9b2aa,#5b5550);border:2px solid rgba(255,255,255,.6)}
  .contact-card .avatar{left:16px;top:24px;width:66px;height:66px}
  .contact-card__name{position:absolute;left:106px;top:43px;font-size:22px;font-weight:300;letter-spacing:-.4px}
  .contact-card--preview .contact-card__name{left:111px;top:26px}
  .contact-card__preview{position:absolute;left:111px;top:62px;font-size:22px;font-weight:500;letter-spacing:-.4px}
  .action-btn{position:absolute;top:34px;height:51px;border-radius:6px;color:var(--white);display:flex;align-items:center;justify-content:center;gap:8px;font-size:21px;font-weight:400;letter-spacing:-.3px}
  .action-btn--start{left:324px;width:106px}
  .action-btn--turn{left:293px;width:137px;background:var(--purple)}
  .action-btn--blue{background:var(--blue)}
  .action-btn--orange{background:var(--orange)}
  .footer-bar{position:absolute;left:0;top:916px;width:100%;height:132px;border-top:1px solid var(--line);background:var(--white)}
  .hidden-btn{position:absolute;left:94px;top:20px;width:296px;height:64px;border-radius:32px;background:linear-gradient(90deg,var(--teal-2),#2ef4dc);color:var(--white);display:flex;align-items:center;gap:30px;padding-left:28px;font-size:22px;font-weight:500;letter-spacing:.3px}
  .chat-title{position:absolute;left:0;width:100%;top:18px;text-align:center;font-size:21px;font-weight:400;letter-spacing:-.3px}
  .nav-bar .avatar{left:53px;top:2px;width:39px;height:39px}
  .thread{position:absolute;left:0;top:113px;width:100%;height:803px;background:linear-gradient(160deg,#f9f9fa,#f2f2f3)}
  .timestamp{position:absolute;left:0;width:100%;text-align:center;font-size:15px;color:var(--muted);font-weight:300}
  .bubble{position:absolute;font-size:20px;font-weight:300;letter-spacing:-.4px;line-height:28px;padding:0 24px;display:flex;align-items:center}
  .bubble--in{left:21px;background:var(--white);color:var(--ink-soft);border-radius:6px}
  .bubble--out{right:21px;background:linear-gradient(90deg,var(--teal-2),#2ef1da);color:var(--white);border-radius:6px;justify-content:center}
  .bubble__tail{position:absolute}
  .composer{position:absolute;left:0;top:916px;width:100%;height:132px;background:var(--white);border-top:1px solid var(--line)}
  .composer__add{position:absolute;left:14px;top:22px}
  .composer__input{position:absolute;left:68px;top:16px;width:346px;height:52px;border:1.5px solid var(--line);border-radius:26px;display:flex;align-items:center;padding-left:22px;gap:10px;font-size:19px;font-weight:300;color:#c3c6cb}
  .composer__caret{width:2px;height:26px;background:#c3c6cb}
  .composer__send{position:absolute;left:423px;top:24px}
</style>
</head>
<body>

<section class="screen screen--contacts">
  <div class="status-bar">
    <span class="status-bar__time">9:41</span>
    <div class="status-bar__icons">
      <svg width="22" height="16" viewBox="0 0 22 16"><path d="M1 5.5a14 14 0 0 1 20 0M4.5 9a9 9 0 0 1 13 0M8 12.3a4 4 0 0 1 6 0" stroke="#111" stroke-width="2.2" fill="none" stroke-linecap="round"/><circle cx="11" cy="14.6" r="1.4" fill="#111"/></svg>
      <svg width="32" height="15" viewBox="0 0 32 15"><rect x="1" y="1" width="27" height="13" rx="3.5" stroke="#111" stroke-width="1.5" fill="none"/><rect x="3" y="3" width="23" height="9" rx="2" fill="#111"/><rect x="29.5" y="5" width="2" height="5" rx="1" fill="#111"/></svg>
    </div>
  </div>
  <header class="nav-bar">
    <svg class="nav-bar__back" width="14" height="26" viewBox="0 0 14 26"><path d="M12 2 2 13l10 11" stroke="#333" stroke-width="3" fill="none" stroke-linecap="round" stroke-linejoin="round"/></svg>
    <div class="nav-bar__title"><span class="brand-dot"></span>Who you’ve met</div>
    <div class="nav-bar__actions">
      <svg width="32" height="32" viewBox="0 0 32 32"><circle cx="14" cy="14" r="11" stroke="#333" stroke-width="2.6" fill="none"/><path d="M22 22l7 7" stroke="#333" stroke-width="2.8" stroke-linecap="round"/></svg>
      <svg width="32" height="32" viewBox="0 0 32 32"><circle cx="16" cy="16" r="10.5" stroke="#333" stroke-width="6" fill="none" stroke-dasharray="4.2 4.05"/><circle cx="16" cy="16" r="9" fill="#333"/><circle cx="16" cy="16" r="4" fill="#fff"/></svg>
    </div>
  </header>

  <div class="contact-list">
    <article class="contact-card" style="top:32px">
      <svg class="contact-card__blob" width="70" height="114" viewBox="0 0 70 114"><defs><linearGradient id="gBlue" x1="0" y1="0" x2="0" y2="1"><stop offset="0" stop-color="#2fd3fb"/><stop offset="1" stop-color="#3aa6f8"/></linearGradient></defs><path d="M8 0H24C50 14 66 40 68 70L66 114H8Q0 114 0 106V8Q0 0 8 0Z" fill="url(#gBlue)"/></svg>
      <div class="avatar" role="img" aria-label="Portrait photo of Marco Hale"></div>
      <span class="contact-card__name">Marco Hale</span>
      <div class="action-btn action-btn--start action-btn--blue">
        <svg width="28" height="28" viewBox="0 0 28 28"><path d="M4 26V3M4 4h18l-4 6 4 6H4M1 26h8" stroke="#fff" stroke-width="2.2" fill="none" stroke-linejoin="round"/></svg>Start
      </div>
    </article>

    <article class="contact-card" style="top:160px">
      <svg class="contact-card__blob" width="70" height="114" viewBox="0 0 70 114"><path d="M8 0H24C50 14 66 40 68 70L66 114H8Q0 114 0 106V8Q0 0 8 0Z" fill="var(--orange)"/></svg>
      <div class="avatar" role="img" aria-label="Portrait photo of Nora Ellis"></div>
      <span class="contact-card__name">Nora Ellis</span>
      <div class="action-btn action-btn--start action-btn--orange">
        <svg width="28" height="28" viewBox="0 0 28 28"><path d="M4 26V3M4 4h18l-4 6 4 6H4M1 26h8" stroke="#fff" stroke-width="2.2" fill="none" stroke-linejoin="round"/></svg>Start
      </div>
    </article>

    <article class="contact-card" style="top:288px">
      <svg class="contact-card__blob" width="70" height="114" viewBox="0 0 70 114"><path d="M8 0H24C50 14 66 40 68 70L66 114H8Q0 114 0 106V8Q0 0 8 0Z" fill="var(--purple)"/></svg>
      <div class="avatar" role="img" aria-label="Portrait photo of Ivy Porter"></div>
      <span class="contact-card__name">Ivy Porter</span>
      <div class="action-btn action-btn--turn">
        <svg width="26" height="28" viewBox="0 0 26 28"><path d="M4 27V5h16M16 1l5 4-5 4" stroke="#fff" stroke-width="2.4" fill="none" stroke-linejoin="round" stroke-linecap="round"/></svg>Your Turn
      </div>
    </article>

    <article class="contact-card contact-card--preview" style="top:416px">
      <svg class="contact-card__blob" width="70" height="114" viewBox="0 0 70 114"><path d="M8 0H24C50 14 66 40 68 70L66 114H8Q0 114 0 106V8Q0 0 8 0Z" fill="var(--teal)"/></svg>
      <div class="avatar" role="img" aria-label="Portrait photo of Clara Weston"></div>
      <span class="contact-card__name">Clara Weston</span>
      <span class="contact-card__preview">Great Idea...</span>
    </article>

    <article class="contact-card contact-card--preview" style="top:544px">
      <svg class="contact-card__blob" width="70" height="114" viewBox="0 0 70 114"><path d="M8 0H24C50 14 66 40 68 70L66 114H8Q0 114 0 106V8Q0 0 8 0Z" fill="var(--red)"/></svg>
      <div class="avatar" role="img" aria-label="Portrait photo of Owen Marsh"></div>
      <span class="contact-card__name">Owen Marsh</span>
      <span class="contact-card__preview">Cool Meeting...</span>
    </article>

    <article class="contact-card contact-card--preview" style="top:672px">
      <svg class="contact-card__blob" width="70" height="114" viewBox="0 0 70 114"><path d="M8 0H24C50 14 66 40 68 70L66 114H8Q0 114 0 106V8Q0 0 8 0Z" fill="var(--yellow)"/></svg>
      <div class="avatar" role="img" aria-label="Portrait photo of Lena Ortiz"></div>
      <span class="contact-card__name">Lena Ortiz</span>
      <span class="contact-card__preview">Good Speeche...</span>
    </article>
  </div>

  <footer class="footer-bar">
    <div class="hidden-btn">
      <svg width="34" height="26" viewBox="0 0 34 26"><path d="M2 13C7 5 12 3 17 3s10 2 15 10c-5 8-10 10-15 10S7 21 2 13Z" stroke="#fff" stroke-width="2.6" fill="none"/><circle cx="17" cy="13" r="4.5" stroke="#fff" stroke-width="2.6" fill="none"/><path d="M6 24 28 2" stroke="#fff" stroke-width="2.6" stroke-linecap="round"/></svg>
      HIDDEN (52)
    </div>
  </footer>
</section>

<section class="screen screen--chat">
  <div class="status-bar">
    <span class="status-bar__time">9:41</span>
    <div class="status-bar__icons">
      <svg width="22" height="16" viewBox="0 0 22 16"><path d="M1 5.5a14 14 0 0 1 20 0M4.5 9a9 9 0 0 1 13 0M8 12.3a4 4 0 0 1 6 0" stroke="#111" stroke-width="2.2" fill="none" stroke-linecap="round"/><circle cx="11" cy="14.6" r="1.4" fill="#111"/></svg>
      <svg width="32" height="15" viewBox="0 0 32 15"><rect x="1" y="1" width="27" height="13" rx="3.5" stroke="#111" stroke-width="1.5" fill="none"/><rect x="3" y="3" width="23" height="9" rx="2" fill="#111"/><rect x="29.5" y="5" width="2" height="5" rx="1" fill="#111"/></svg>
    </div>
  </div>
  <header class="nav-bar">
    <svg class="nav-bar__back" width="14" height="26" viewBox="0 0 14 26"><path d="M12 2 2 13l10 11" stroke="#333" stroke-width="3" fill="none" stroke-linecap="round" stroke-linejoin="round"/></svg>
    <div class="avatar" role="img" aria-label="Portrait photo of Marco Hale"></div>
    <h1 class="chat-title">Marco Hale</h1>
  </header>

  <div class="thread">
    <p class="timestamp" style="top:16px">Today at 5:03 PM</p>
    <div class="bubble bubble--in" style="top:60px;width:247px;height:63px">Hey! How's it going?</div>
    <div class="bubble bubble--in" style="top:135px;width:322px;height:86px;border-bottom-left-radius:0">Would you like to go the coffee tonight?
      <svg class="bubble__tail" style="left:0;top:86px" width="14" height="14" viewBox="0 0 14 14"><path d="M0 0H14L0 14Z" fill="#fff"/></svg>
    </div>
    <p class="timestamp" style="top:262px">5:33 PM</p>
    <div class="bubble bubble--out" style="top:306px;width:142px;height:64px">OK, sure !</div>
    <div class="bubble bubble--out" style="top:379px;width:275px;height:64px;border-bottom-right-radius:0">When do you want to go?
      <svg class="bubble__tail" style="right:0;top:64px" width="18" height="14" viewBox="0 0 18 14"><path d="M0 0H18V14Z" fill="#2ef1da"/></svg>
    </div>
  </div>

  <footer class="composer">
    <svg class="composer__add" width="40" height="40" viewBox="0 0 40 40"><circle cx="20" cy="20" r="18" stroke="var(--teal-2)" stroke-width="2.4" fill="none"/><path d="M20 10v20M10 20h20" stroke="var(--teal-2)" stroke-width="2.4" stroke-linecap="round"/></svg>
    <div class="composer__input"><span class="composer__caret"></span>Type a message...</div>
    <svg class="composer__send" width="44" height="36" viewBox="0 0 44 36"><path d="M1 14 43 1 22 35 19 19Z" fill="var(--teal-2)"/><path d="M19 19 43 1" stroke="#fff" stroke-width="2"/></svg>
  </footer>
</section>

</body>
</html>
```